Animal Eye Clinic needs a Business card

We are a new veterinary ophthalmology practice (Ridgeline Pet Vision Care) and we need a business card designed. We only see animal eyes - we are not a regular veterinary clinic. We already have a logo. We are looking for a professional, good looking business card to hand out to our clients. We are looking for something simple but professional and contemporary. Our logo is likely the only picture/graphic that needs to be on the card.
Updates

Contact Information for Business Card

Delia Vossman, BSc, DVM, MSc, DipACVO
Veterinary Ophthalmologist

Phone: 250.418.3927
Email: ridgelinepetvisioncare@mailbox-example.net
Website: ridgelinepetvisioncare-example.net
Address: 1874 Thornbury Rd
Kelowna, BC, V1X 4M9

Colors

Designer to choose colors to be used in the design.

Requirements
Must have
• Our logo (attached)

```html
<!DOCTYPE html>
<html lang="en">
<head>
<meta charset="utf-8">
<title>Ridgeline Pet Vision Care – Business Card</title>
<link href="https://fonts.googleapis.com/css2?family=Roboto:wght@400;500;700&display=swap" rel="stylesheet">
<style>
  :root {
    --teal: #1b95a5;
    --ink: #232323;
    --grey-text: #5e5e5e;
    --paper: #ffffff;
    --backdrop: #d9dadc;
  }
  * { box-sizing: border-box; margin: 0; padding: 0; }
  html, body {
    width: 1200px; height: 800px; overflow: hidden;
    background: var(--backdrop);
    font-family: "Roboto", Arial, sans-serif;
  }
  .canvas { position: relative; width: 1200px; height: 800px; }

  .card {
    position: absolute;
    width: 600px; height: 343px;
    background: var(--paper);
    overflow: hidden;
    box-shadow: 0 4px 14px rgba(0,0,0,0.18);
  }

  /* Front */
  .card--front { left: 540px; top: 50px; }
  .front-panel { position: absolute; inset: 0; }
  .front-brand {
    position: absolute; left: 300px; top: 128px;
    display: flex; align-items: center; gap: 16px;
  }
  .brand-dot {
    width: 64px; height: 64px; border-radius: 50%;
    background: var(--teal); flex: none;
  }
  .brand-name {
    color: var(--teal); font-weight: 500;
    font-size: 22px; line-height: 1.15; letter-spacing: 0.08em;
    text-transform: uppercase;
  }

  /* Back */
  .card--back { left: 60px; top: 400px; padding: 34px 40px; }
  .back-brand { display: flex; align-items: center; gap: 14px; }
  .back-brand .brand-dot { width: 44px; height: 44px; }
  .back-brand .brand-name { font-size: 20px; }

  .holder { margin-top: 30px; }
  .holder-name {
    color: var(--teal); font-weight: 700; font-size: 22px;
    text-transform: uppercase; letter-spacing: 0.01em;
  }
  .holder-creds { font-size: 14px; font-weight: 700; margin-left: 4px; text-transform: none; }
  .holder-title { color: var(--grey-text); font-size: 17px; margin-top: 2px; }

  .address { color: var(--grey-text); font-size: 16px; line-height: 1.25; margin-top: 18px; }
  .contact-list { list-style: none; margin-top: 6px; color: var(--grey-text); font-size: 16px; line-height: 1.3; }
  .contact-list li { display: flex; align-items: center; gap: 8px; }
  .contact-icon { width: 14px; height: 14px; flex: none; fill: none; stroke: var(--teal); stroke-width: 1.6; }
  .contact-icon--solid { fill: var(--teal); stroke: none; }
</style>
</head>
<body>
<main class="canvas">

  <section class="card card--front" aria-label="Card front">
    <svg class="front-panel" width="600" height="343" viewBox="0 0 600 343" aria-hidden="true">
      <path d="M150 0 L600 0 L600 343 L230 343 Q120 170 150 0 Z" fill="var(--teal)"/>
      <path d="M175 0 L600 0 L600 343 L255 343 Q150 170 175 0 Z" fill="var(--ink)"/>
    </svg>
    <div class="front-brand">
      <span class="brand-dot" aria-hidden="true"></span>
      <p class="brand-name">Ridgeline<br>Pet Vision Care</p>
    </div>
  </section>

  <section class="card card--back" aria-label="Card back">
    <div class="back-brand">
      <span class="brand-dot" aria-hidden="true"></span>
      <p class="brand-name">Ridgeline Pet Vision Care</p>
    </div>

    <div class="holder">
      <h1 class="holder-name">Delia Vossman <span class="holder-creds">BSc, DVM, MSc, DipACVO</span></h1>
      <p class="holder-title">Veterinary Ophthalmologist</p>
    </div>

    <p class="address">1874 Thornbury Rd<br>Kelowna, BC, V1X 4M9</p>

    <ul class="contact-list">
      <li>
        <svg class="contact-icon contact-icon--solid" viewBox="0 0 16 16" aria-hidden="true"><path d="M3 1h3l1.5 4-2 1.2a9 9 0 0 0 4.3 4.3L11 8.5l4 1.5v3a2 2 0 0 1-2 2A12 12 0 0 1 1 3a2 2 0 0 1 2-2z"/></svg>
        250.418.3927
      </li>
      <li>
        <svg class="contact-icon" viewBox="0 0 16 16" aria-hidden="true"><rect x="1" y="3" width="14" height="10"/><path d="M1 3l7 6 7-6"/></svg>
        ridgelinepetvisioncare@mailbox-example.net
      </li>
      <li>
        <svg class="contact-icon" viewBox="0 0 16 16" aria-hidden="true"><circle cx="8" cy="8" r="7"/><ellipse cx="8" cy="8" rx="3" ry="7"/><path d="M1 8h14"/></svg>
        ridgelinepetvisioncare-example.net
      </li>
    </ul>
  </section>

</main>
</body>
</html>
```